Business Card Design

WE are looking for a premium quality Business Cards for a Law Firm . Copies of our current business card is attached.

Contact Information for Business Card

xyz

```html
<!DOCTYPE html>
<html lang="en">
<head>
<meta charset="utf-8">
<title>Ashcroft Lawyers — Business Cards</title>
<link rel="stylesheet" href="https://fonts.googleapis.com/css2?family=Tinos:wght@400;700&display=swap">
<style>
  :root {
    --stage: #222222;
    --green: #0d2a1e;
    --green-deep: #0a2219;
    --gold: #c9a961;
    --white: #ffffff;
    --rule: rgba(255,255,255,0.75);
  }
  * { box-sizing: border-box; margin: 0; padding: 0; }
  html, body {
    width: 1200px; height: 780px; overflow: hidden;
    background: var(--stage);
    font-family: "Tinos", "Times New Roman", serif;
  }
  .canvas { position: relative; width: 1200px; height: 780px; }

  .card {
    position: absolute; width: 560px; height: 340px;
    overflow: hidden; box-shadow: 0 18px 40px rgba(0,0,0,0.55);
  }

  /* ---------- Back card ---------- */
  .card-back { left: 80px; top: 40px; background: var(--green); }
  .card-back .pattern-area { position: absolute; inset: 0; }
  .card-back .brand {
    position: absolute; top: 38px; left: 0; right: 0;
    display: flex; align-items: center; justify-content: center; gap: 14px;
  }
  .brand-circle {
    width: 58px; height: 58px; border-radius: 50%;
    border: 4px solid var(--gold); flex: none;
  }
  .brand-name {
    font-weight: 700; font-size: 28px; line-height: 1.05;
    letter-spacing: 2px; text-transform: uppercase;
  }
  .card-back .brand-name { color: var(--white); }
  .tagline-band {
    position: absolute; left: 0; right: 0; top: 140px; height: 30px;
    background: var(--gold); color: var(--white);
    display: flex; align-items: center; justify-content: center;
    font-weight: 700; font-size: 15px; letter-spacing: 1px; text-transform: uppercase;
  }
  .offices {
    position: absolute; left: 20px; right: 20px; top: 196px; bottom: 22px;
    display: grid; grid-template-columns: 1fr 1fr 1fr;
  }
  .office {
    padding: 4px 10px; text-align: center; color: var(--white);
    font-weight: 700; font-size: 12.5px; line-height: 1.45;
  }
  .office + .office { border-left: 1.5px solid var(--rule); }
  .office-city {
    color: var(--gold); font-size: 17px; letter-spacing: 1px;
    text-transform: uppercase; margin-bottom: 4px;
  }
  .office-phone { display: inline-flex; align-items: center; gap: 5px; }
  .icon { width: 13px; height: 13px; flex: none; }

  /* ---------- Front card ---------- */
  .card-front { left: 560px; top: 400px; background: var(--green-deep); }
  .card-front .swoosh { position: absolute; inset: 0; }
  .accent-bar {
    position: absolute; left: 0; top: 28px; width: 14px; height: 70px; background: var(--gold);
  }
  .person { position: absolute; left: 34px; top: 24px; color: var(--white); }
  .person-name {
    color: var(--gold); font-weight: 700; font-size: 32px;
    letter-spacing: 1px; text-transform: uppercase; line-height: 1;
  }
  .person-role { font-weight: 700; font-size: 15px; line-height: 1.3; margin-top: 6px; }
  .address {
    position: absolute; left: 60px; top: 140px; font-style: normal;
    color: var(--white); font-weight: 700; font-size: 14.5px; line-height: 1.35;
  }
  .contacts {
    position: absolute; left: 60px; top: 224px; list-style: none;
    color: var(--white); font-weight: 700; font-size: 13.5px; line-height: 1.55;
  }
  .contacts li { display: flex; align-items: center; gap: 8px; }
  .card-front .brand {
    position: absolute; left: 372px; top: 120px; width: 180px;
    display: flex; align-items: center; gap: 10px;
  }
  .card-front .brand-circle { width: 46px; height: 46px; border-width: 4px; }
  .card-front .brand-name { color: var(--green); font-size: 20px; letter-spacing: 1.5px; }
</style>
</head>
<body>
<main class="canvas">

  <section class="card card-back" aria-label="Business card back">
    <svg class="pattern-area" viewBox="0 0 560 340" role="img" aria-label="Faint repeating circle monogram pattern across the green background">
      <rect width="560" height="340" fill="#0f2e21"/>
    </svg>
    <div class="brand">
      <span class="brand-circle"></span>
      <span class="brand-name">Ashcroft<br>Lawyers</span>
    </div>
    <div class="tagline-band">Clear counsel. Lasting results. Every time</div>
    <div class="offices">
      <div class="office">
        <div class="office-city">Melbourne</div>
        Level 12, 88 Harbour Street,<br>MELBOURNE, VIC 3000<br>
        <span class="office-phone">
          <svg class="icon" viewBox="0 0 24 24"><path fill="#c9a961" d="M6.6 10.8a15 15 0 0 0 6.6 6.6l2.2-2.2c.3-.3.7-.4 1-.2 1.1.4 2.3.6 3.6.6.6 0 1 .4 1 1V20c0 .6-.4 1-1 1A17 17 0 0 1 3 4c0-.6.4-1 1-1h3.5c.6 0 1 .4 1 1 0 1.2.2 2.4.6 3.6.1.3 0 .7-.2 1z"/></svg>
          +61 03 5550 1234</span>
      </div>
      <div class="office">
        <div class="office-city">Sydney</div>
        Level 9, Kestrel House<br>22 River Road<br>PARRAMATTA, NSW 2150<br>
        <span class="office-phone">
          <svg class="icon" viewBox="0 0 24 24"><path fill="#c9a961" d="M6.6 10.8a15 15 0 0 0 6.6 6.6l2.2-2.2c.3-.3.7-.4 1-.2 1.1.4 2.3.6 3.6.6.6 0 1 .4 1 1V20c0 .6-.4 1-1 1A17 17 0 0 1 3 4c0-.6.4-1 1-1h3.5c.6 0 1 .4 1 1 0 1.2.2 2.4.6 3.6.1.3 0 .7-.2 1z"/></svg>
          +61 02 5550 2841</span>
      </div>
      <div class="office">
        <div class="office-city">Perth</div>
        Level 18, Beacon Tower<br>75 Hay Crescent<br>PERTH, WA 6000<br>
        <span class="office-phone">
          <svg class="icon" viewBox="0 0 24 24"><path fill="#c9a961" d="M6.6 10.8a15 15 0 0 0 6.6 6.6l2.2-2.2c.3-.3.7-.4 1-.2 1.1.4 2.3.6 3.6.6.6 0 1 .4 1 1V20c0 .6-.4 1-1 1A17 17 0 0 1 3 4c0-.6.4-1 1-1h3.5c.6 0 1 .4 1 1 0 1.2.2 2.4.6 3.6.1.3 0 .7-.2 1z"/></svg>
          +61 08 5550 3907</span>
      </div>
    </div>
  </section>

  <section class="card card-front" aria-label="Business card front">
    <svg class="swoosh" viewBox="0 0 560 340" aria-hidden="true">
      <path d="M400 0 C 330 110, 340 250, 470 340 L560 340 L560 0 Z" fill="#ffffff"/>
      <path d="M372 0 C 332 100, 336 200, 382 255" fill="none" stroke="#ffffff" stroke-width="5"/>
      <path d="M388 0 C 350 95, 350 190, 394 250" fill="none" stroke="#0a2219" stroke-width="4"/>
      <path d="M332 150 C 342 250, 388 315, 470 340 L442 340 C 372 310, 334 240, 332 150 Z" fill="#c9a961"/>
    </svg>
    <div class="accent-bar"></div>
    <div class="person">
      <div class="person-name">Rohan Mehta</div>
      <div class="person-role">Director and Principal Solicitor<br>MBA, Juris Doctor</div>
    </div>
    <address class="address">
      Suite 310, Ellery Chambers,<br>214 Lonsdale Lane,<br>Melbourne VIC 3000
    </address>
    <ul class="contacts">
      <li><svg class="icon" viewBox="0 0 24 24"><path fill="#c9a961" d="M6.6 10.8a15 15 0 0 0 6.6 6.6l2.2-2.2c.3-.3.7-.4 1-.2 1.1.4 2.3.6 3.6.6.6 0 1 .4 1 1V20c0 .6-.4 1-1 1A17 17 0 0 1 3 4c0-.6.4-1 1-1h3.5c.6 0 1 .4 1 1 0 1.2.2 2.4.6 3.6.1.3 0 .7-.2 1z"/></svg>+61 7 5550 4418</li>
      <li><svg class="icon" viewBox="0 0 24 24"><rect x="6" y="2" width="12" height="20" rx="2" fill="none" stroke="#c9a961" stroke-width="2"/><circle cx="12" cy="18" r="1.2" fill="#c9a961"/></svg>+61 0400 555 019</li>
      <li><svg class="icon" viewBox="0 0 24 24"><circle cx="12" cy="12" r="9" fill="none" stroke="#c9a961" stroke-width="2"/><path d="M3 12h18M12 3c3 3 3 15 0 18M12 3c-3 3-3 15 0 18" fill="none" stroke="#c9a961" stroke-width="1.6"/></svg>www.ashcroftlawyers.com.au</li>
      <li><svg class="icon" viewBox="0 0 24 24"><rect x="2" y="5" width="20" height="14" rx="1.5" fill="none" stroke="#c9a961" stroke-width="2"/><path d="M2 6l10 7 10-7" fill="none" stroke="#c9a961" stroke-width="2"/></svg>rohan@ashcroftlawyers.com.au</li>
    </ul>
    <div class="brand">
      <span class="brand-circle"></span>
      <span class="brand-name">Ashcroft<br>Lawyers</span>
    </div>
  </section>

</main>
</body>
</html>
```